Letterhead Design for Law Firm

**Edit: I have added the photo of a bottom that I like.

------
We are looking for a re-design of our new letterhead. The letterhead is for a law firm and will be used for digital and traditionally printed correspondence.

Here are some suggestions:

- Please use colours are #8ec900 and simple black.
- Please do not use any type of "waves" at the bottom of the page. This is not in style at all.
- Please stay modern yet conservative.
- Please use font Segoe UI Light or similar if you can
- Avoid clipart or illustrations.
- Utilize ample white space in the layout so the design looks clean and information is easy to read at a glance. Don't overcrowd the letterhead.
- Make sure the letterhead design is consistent with our brand identity (see corvelith.ca)
-Please, no black headers or footers.

I am attaching my current letterhead and signature for your convenience.

Remember, the letterhead is an extension of our professional identity. We are a successful firm and trial lawyers who correspond with insurers, judges, lawyers, courts, clients, etc. Make it new, modern, attractive, yet powerful and conservative.

It needs to be easily printable. I would like the bleed removed in print so the black bar the bottom crosses the page (but the text is not near the edges)
Updates

Low design quality

Target Market(s)

Clients, Government Offices, Judiciary, Lawyers, Insurance Companies, Colleagues.

Industry/Entity Type

Law

Other font styles liked:
• Segoe UI LIght, Calibri Light,

Colors
00AB8E
00BBA5
67D7C9
C6EFE9
E9F9F6

Requirements
Must have
• Everything that is on the letterhead now.
Nice to have
• Cutting Edge design, yet conservative.
Should not have
• law firm cliche design, images,

```html
<!DOCTYPE html>
<html lang="en">
<head>
<meta charset="utf-8">
<title>Ardenne Personal Injury Lawyers – Letterhead</title>
<link rel="stylesheet" href="https://fonts.googleapis.com/css2?family=Open+Sans:wght@300;400;600;700&display=swap">
<style>
  :root {
    --brand-green: #8ec900;
    --ink: #000000;
    --text: #222222;
    --paper: #fdfdfd;
  }
  * { margin: 0; padding: 0; box-sizing: border-box; }
  html, body {
    width: 849px; height: 1200px; overflow: hidden; background: var(--paper);
  }
  .letterhead {
    position: relative; width: 849px; height: 1200px; background: var(--paper);
    font-family: "Open Sans", "Segoe UI", sans-serif; color: var(--text);
  }
  .side-band { position: absolute; left: 0; top: 0; }

  .firm-name {
    position: absolute; left: 62px; top: 52px;
    font-weight: 400; color: var(--ink); line-height: 1;
  }
  .firm-name .name { display: block; font-size: 66px; letter-spacing: 4px; }
  .firm-name .tagline { display: block; font-size: 17.5px; letter-spacing: 1.6px; margin-top: 10px; }

  .practice {
    position: absolute; left: 653px; top: 50px;
    font-weight: 300; font-size: 13.4px; line-height: 16.5px; list-style: none;
  }
  .practice-title { font-weight: 700; color: var(--brand-green); font-size: 13.4px; line-height: 18px; }

  .contact-row {
    position: absolute; top: 1106px; left: 0; height: 24px; width: 849px;
    font-weight: 300; font-size: 12.8px;
  }
  .contact-item { position: absolute; display: flex; align-items: center; height: 24px; white-space: nowrap; }
  .contact-item svg { flex: none; }
  .contact-item .label { font-weight: 400; margin-right: 4px; }
  .web   { left: 66px; }   .web svg { margin-right: 7px; }
  .mail  { left: 194px; }  .mail svg { margin-right: 10px; }
  .phone { left: 353px; }  .phone svg { margin-right: 9px; }
  .fax   { left: 482px; }  .fax svg { margin-right: 9px; }
  .clerk { left: 607px; }  .clerk svg { margin-right: 8px; }
  .address { left: 290px; top: 32px; }
  .address svg { margin-right: 6px; }
</style>
</head>
<body>
<div class="letterhead">

  <svg class="side-band" width="36" height="1200" viewBox="0 0 36 1200" aria-hidden="true">
    <polygon points="0,0 36,46 36,875 0,841" fill="var(--brand-green)"/>
    <polygon points="0,841 36,875 36,1173 8,1200 0,1200" fill="var(--ink)"/>
  </svg>

  <h1 class="firm-name">
    <span class="name">ARDENNE</span>
    <span class="tagline">PERSONAL INJURY LAWYERS</span>
  </h1>

  <ul class="practice">
    <li class="practice-title">Practice Restricted:</li>
    <li>Serious Personal Injury</li>
    <li>Wrongful Death Litigation</li>
    <li>Long-Term Disability Litigation</li>
    <li>Wrongful Dismissal Litigation</li>
    <li>Employee Terminations</li>
  </ul>

  <div class="contact-row">
    <div class="contact-item web">
      <svg width="21" height="21" viewBox="0 0 24 24" aria-hidden="true">
        <circle cx="12" cy="12" r="10.5" fill="none" stroke="var(--ink)" stroke-width="2.2"/>
        <ellipse cx="12" cy="12" rx="4.5" ry="10.5" fill="none" stroke="var(--ink)" stroke-width="2"/>
        <line x1="1.5" y1="12" x2="22.5" y2="12" stroke="var(--ink)" stroke-width="2"/>
        <line x1="3" y1="6.5" x2="21" y2="6.5" stroke="var(--ink)" stroke-width="2"/>
        <line x1="3" y1="17.5" x2="21" y2="17.5" stroke="var(--ink)" stroke-width="2"/>
      </svg>
      <span>www.corvelith.ca</span>
    </div>
    <div class="contact-item mail">
      <svg width="22" height="15" viewBox="0 0 22 15" aria-hidden="true">
        <rect x="0.5" y="0.5" width="21" height="14" fill="var(--ink)"/>
        <polyline points="1.5,1.5 11,8.5 20.5,1.5" fill="none" stroke="var(--paper)" stroke-width="1.4"/>
        <line x1="1.5" y1="13.5" x2="8.5" y2="7" stroke="var(--paper)" stroke-width="1.4"/>
        <line x1="20.5" y1="13.5" x2="13.5" y2="7" stroke="var(--paper)" stroke-width="1.4"/>
      </svg>
      <span>mira@corvelith.ca</span>
    </div>
    <div class="contact-item phone">
      <svg width="17" height="24" viewBox="0 0 17 24" aria-hidden="true">
        <path d="M4 1 L8 6 L5.5 9 Q6.5 14 10.5 17 L13 15 L16.5 20 L13.5 23 Q6 22 2.5 14 Q0 7 1.5 3 Z" fill="var(--ink)"/>
      </svg>
      <span>905-555-0142</span>
    </div>
    <div class="contact-item fax">
      <svg width="24" height="20" viewBox="0 0 24 20" aria-hidden="true">
        <path d="M5 1 H17 L19 3 V10 H5 Z" fill="none" stroke="var(--ink)" stroke-width="2"/>
        <line x1="8" y1="5" x2="15" y2="5" stroke="var(--ink)" stroke-width="1.5"/>
        <line x1="8" y1="7.5" x2="15" y2="7.5" stroke="var(--ink)" stroke-width="1.5"/>
        <path d="M1 10 H23 V19 H1 Z" fill="var(--ink)"/>
        <rect x="4" y="13" width="16" height="2" fill="var(--paper)"/>
      </svg>
      <span>905-555-0187</span>
    </div>
    <div class="contact-item clerk">
      <svg width="18" height="22" viewBox="0 0 18 22" aria-hidden="true">
        <circle cx="9" cy="6" r="5.5" fill="var(--ink)"/>
        <path d="M0 21 Q1 13 6 12.5 L9 15.5 L12 12.5 Q17 13 18 21 Z" fill="var(--ink)"/>
      </svg>
      <span class="label">File Clerk:</span><span>Mira Castellan</span>
    </div>
    <div class="contact-item address">
      <svg width="15" height="19" viewBox="0 0 15 19" aria-hidden="true">
        <path d="M7.5 0.5 A7 7 0 0 1 14.5 7.5 C14.5 12 7.5 18.5 7.5 18.5 C7.5 18.5 0.5 12 0.5 7.5 A7 7 0 0 1 7.5 0.5 Z" fill="var(--ink)"/>
        <circle cx="7.5" cy="7.3" r="3" fill="var(--paper)"/>
      </svg>
      <span>40 Alder Street W., Suite 1210 Hamilton, ON&nbsp; L8P 2B7</span>
    </div>
  </div>

</div>
</body>
</html>
```